Label design - Superfood blend

We are a family owned nutrition company with big ambitions. Our goal is to develop a range of 100% natural supplements for women, inspired by nature & modern technology that helps them meet their nutritional needs while nourishing them from within. All our products are junk free because we believe that that’s how nature intended it. We also produce products through a sustainable process and only use biodegradable packaging for our products (See link - https://www.loamwrap.org.uk/biodegradable-stand-pouch-250g-kraft)

Our brand style is modern and minimalist. This same style will be reflected in our social media, website and we want it to be represented through the label designs for our product packaging.

We want some creative designers to design a label that is true to our style (See attached packaging brief with designs we like) and displays our values of Premium, High Quality, Organic Real Food supplements focused on women. I have provided examples in the attached brief, but please only use as inspiration, I dont want any of them to be copied (sorry have had my fingers burnt already !)
Updates

Hello all, Please note this design is for a LABEL and not the whole package. We will have a 500gm biodegradable brown package, and we will have a label (which is what this project is about) that will be stuck on the front. The size of the label will be a rectangle (unless you come up with a new shape) in the size 20cm * 15cm. Please do not submit designs for the WHOLE from of the package, as we dont intend to have printed packages. Regards

Hello all, I have added a new logo version to the attachments, could you please also try that version. Could you also please look at the new sliders. We are only looking for a minimlaist theme. If you dont know what that means, please do feel free to ask, I would be happy to supply examples. Minimalist designs, means clean, modern, upmarket, elegant designs. It does not use too many colors and mostly sticks to a combination of black and white with colors used sparingly. See some below for your reference anyway. https://www.pitchloft.co.uk/design/13359317 https://www.pitchloft.co.uk/design/17270649 https://www.pitchloft.co.uk/design/12584145 https://www.pitchloft.co.uk/design/12367479 https://www.snapquilt.com/search/pins/?q=minimalist%20label%20design&rs=rs&eq=&etslf=2809&term_meta[]=minimalist%7Crecentsearch%7Cundefined&term_meta[]=label%7Crecentsearch%7Cundefined&term_meta[]=design%7Crecentsearch%7Cundefined Regards

Target Market(s)

The target market is women between the age 25 to 45, based in UK (mostly based in larger cities in UK). They are typically middle class or higher and would be in demanding jobs and social lives, that requires for them to meet their nutrition needs in convenient, easy to take forms. The women would also be socially conscious and sensitive to issues like women's rights, environmental issues, healthy food, organic food and sustainability etc. I have a much more detailed customer avatar if required

Font styles to use
Serif
Sans Serif
Decorative
Script

Colors
e8e8e8
474747
1b1b1b
add136

Requirements
Must have
• The label, should look minimalist and modern, throw in some out of the box creativity and we have a winner. Creativity will definitely be of importance. Our packaging is a biodegradable brown paper stand up pouch (Example link in product description). So to make it standout from other colorful packaging - being creative would definitely help.
• Please use the color schemes provided in the brief (See attachments). But if you want to experiment I would be open to it, as long as they are still minimalist and does not stray very far from the color given in the brief :)

```html
<!DOCTYPE html>
<html lang="en">
<head>
<meta charset="utf-8">
<title>Tend Thy Core – Label Range</title>
<link rel="stylesheet" href="https://fonts.googleapis.com/css2?family=Montserrat:wght@300;400;600;700&display=swap">
<style>
  :root {
    --canvas: #ffffff;
    --label: #f4f4f4;
    --label-edge: #e2e2e2;
    --ink: #1b1b1b;
    --ink-soft: #474747;
    --muted: #8a8a8a;
    --rule: #9a9a9a;
    --green: #6fae8a;
    --outline: #8c8c8c;
  }
  * { box-sizing: border-box; margin: 0; padding: 0; }
  html, body {
    width: 1200px; height: 857px; overflow: hidden;
    background: var(--canvas);
    font-family: "Montserrat", sans-serif;
    color: var(--ink);
  }
  .range { position: absolute; left: 0; top: 0; width: 1200px; height: 857px; }
  .label {
    position: absolute; top: 377px;
    width: 174px; height: 238px;
    background: var(--label);
    border-radius: 8px;
    box-shadow: 0 0 0 1px var(--label-edge);
  }
  .label:nth-child(1) { left: 109px; }
  .label:nth-child(2) { left: 375px; }
  .label:nth-child(3) { left: 642px; }
  .label:nth-child(4) { left: 909px; }

  .brand {
    position: absolute; left: 10px; top: 8px;
    width: 26px; height: 200px;
    display: flex; flex-direction: column; align-items: center; justify-content: flex-end;
  }
  .brand-dot {
    width: 6px; height: 6px; border-radius: 50%;
    background: var(--green); margin-bottom: 6px;
  }
  .brand-name {
    writing-mode: vertical-rl; transform: rotate(180deg);
    font-size: 18px; font-weight: 400; letter-spacing: 10px; line-height: 1;
    color: var(--ink-soft);
  }

  .title-main {
    position: absolute; left: 55px; top: 62px;
    font-size: 35px; font-weight: 700; line-height: 1; letter-spacing: -1px;
  }
  .title-sub {
    position: absolute; left: 56px; top: 101px;
    font-size: 20px; font-weight: 700; line-height: 1; letter-spacing: -0.4px;
  }
  .is-green { color: var(--green); }
  .is-dark { color: var(--ink); }
  .is-outline { color: transparent; -webkit-text-stroke: 0.8px var(--outline); }

  .tagline {
    position: absolute; left: 56px; top: 129px; width: 104px;
    font-size: 4.2px; font-weight: 400; color: var(--ink-soft); line-height: 1;
    padding-bottom: 3px; border-bottom: 0.5px solid var(--rule);
    white-space: nowrap;
  }
  .ingredients { position: absolute; left: 56px; top: 148px; width: 92px; }
  .ingredients li {
    list-style: none; display: flex;
    font-size: 5.6px; font-weight: 300; color: var(--ink-soft); line-height: 1;
    border-bottom: 0.5px solid var(--rule); padding: 3px 0 2px;
  }
  .ingredients span:first-child { width: 38px; border-right: 0.5px solid var(--ink-soft); margin-right: 6px; }
  .supplement {
    position: absolute; left: 56px; top: 202px;
    font-size: 4.8px; font-weight: 700; letter-spacing: 0.1px; line-height: 1;
  }
  .footer {
    position: absolute; left: 8px; right: 8px; top: 211px; bottom: 0;
    border-top: 0.5px solid var(--rule);
    display: flex; align-items: center; gap: 6px; padding-left: 10px;
  }
  .net-weight { font-size: 4.2px; font-weight: 300; color: var(--ink-soft); line-height: 1.3; width: 26px; }
  .badges { display: flex; gap: 3px; align-items: center; }
  .badge { width: 12px; height: 12px; border-radius: 50%; border: 1px solid var(--ink-soft); }
  .badge.is-soft { border-color: var(--muted); border-width: 0.7px; }
</style>
</head>
<body>
<main class="range">

  <article class="label">
    <div class="brand"><span class="brand-dot"></span><span class="brand-name">NORVELLE</span></div>
    <h1 class="title-main is-green">TEND</h1>
    <h2 class="title-sub is-outline">THY CORE</h2>
    <p class="tagline">Organic Prebiotics And Superfood Blend For Women</p>
    <ul class="ingredients">
      <li><span>Baobab</span><span>Flaxseed</span></li>
      <li><span>Acai Berry</span><span>Maca Powder</span></li>
      <li><span>Goji Berry</span><span>Aronia Berry</span></li>
      <li><span>Camu Camu</span><span>Cinnamon</span></li>
    </ul>
    <p class="supplement">FOOD SUPPLEMENT</p>
    <footer class="footer">
      <p class="net-weight">Net Weight<br>300 gm</p>
      <div class="badges"><span class="badge"></span><span class="badge"></span><span class="badge"></span><span class="badge is-soft"></span><span class="badge is-soft"></span></div>
    </footer>
  </article>

  <article class="label">
    <div class="brand"><span class="brand-dot"></span><span class="brand-name">NORVELLE</span></div>
    <h1 class="title-main is-dark">TEND</h1>
    <h2 class="title-sub is-outline">THY CORE</h2>
    <p class="tagline">Organic Prebiotics And Superfood Blend For Women</p>
    <ul class="ingredients">
      <li><span>Baobab</span><span>Flaxseed</span></li>
      <li><span>Acai Berry</span><span>Maca Powder</span></li>
      <li><span>Goji Berry</span><span>Aronia Berry</span></li>
      <li><span>Camu Camu</span><span>Cinnamon</span></li>
    </ul>
    <p class="supplement">FOOD SUPPLEMENT</p>
    <footer class="footer">
      <p class="net-weight">Net Weight<br>300 gm</p>
      <div class="badges"><span class="badge"></span><span class="badge"></span><span class="badge"></span><span class="badge is-soft"></span><span class="badge is-soft"></span></div>
    </footer>
  </article>

  <article class="label">
    <div class="brand"><span class="brand-dot"></span><span class="brand-name">NORVELLE</span></div>
    <h1 class="title-main is-green">TEND</h1>
    <h2 class="title-sub is-dark">THY CORE</h2>
    <p class="tagline">Organic Prebiotics And Superfood Blend For Women</p>
    <ul class="ingredients">
      <li><span>Baobab</span><span>Flaxseed</span></li>
      <li><span>Acai Berry</span><span>Maca Powder</span></li>
      <li><span>Goji Berry</span><span>Aronia Berry</span></li>
      <li><span>Camu Camu</span><span>Cinnamon</span></li>
    </ul>
    <p class="supplement">FOOD SUPPLEMENT</p>
    <footer class="footer">
      <p class="net-weight">Net Weight<br>300 gm</p>
      <div class="badges"><span class="badge"></span><span class="badge"></span><span class="badge"></span><span class="badge is-soft"></span><span class="badge is-soft"></span></div>
    </footer>
  </article>

  <article class="label">
    <div class="brand"><span class="brand-dot"></span><span class="brand-name">NORVELLE</span></div>
    <h1 class="title-main is-dark">TEND</h1>
    <h2 class="title-sub is-green">THY CORE</h2>
    <p class="tagline">Organic Prebiotics And Superfood Blend For Women</p>
    <ul class="ingredients">
      <li><span>Baobab</span><span>Flaxseed</span></li>
      <li><span>Acai Berry</span><span>Maca Powder</span></li>
      <li><span>Goji Berry</span><span>Aronia Berry</span></li>
      <li><span>Camu Camu</span><span>Cinnamon</span></li>
    </ul>
    <p class="supplement">FOOD SUPPLEMENT</p>
    <footer class="footer">
      <p class="net-weight">Net Weight<br>300 gm</p>
      <div class="badges"><span class="badge"></span><span class="badge"></span><span class="badge"></span><span class="badge is-soft"></span><span class="badge is-soft"></span></div>
    </footer>
  </article>

</main>
</body>
</html>
```